Business card for my new company (Accounting firm)

I need a business card for my new business Brightwell Advisory and Ledger SA. Our services are accounting, tax, audit and financial management. Our customers are small companies, start-ups and new companies. The final design has to show financial security, trust and growth. Please find our logo attached to the business card. Text for the business card: Brightwell Advisory and Ledger SA Tomas Varenholt Director and Founder Certified Accountant Tel. 022 418 57 34 tv@clairevalconseil.ch www.clairevalconseil.ch Rue des Vergières 27 1201 Geneva
Target Market(s)
Our customers are small companies, start-ups and new companies.
Industry/Entity Type
Finance And Accounting
Contact Information for Business Card
Claireval Conseil et Comptes SA
Tomas Varenholt
Directeur et Fondateur
Expert-comptable diplômé
Tél. 022 418 57 34
tv@clairevalconseil.ch
www.clairevalconseil.ch
Rue des Vergières 27
1201 Genève

```html
<!DOCTYPE html>
<html lang="fr">
<head>
<meta charset="utf-8">
<title>Claireval Conseil et Comptes SA – Carte de visite</title>
<link href="https://fonts.googleapis.com/css2?family=Montserrat:wght@600&family=Roboto:wght@400;700&display=swap" rel="stylesheet">
<style>
  :root{
    --bg:#e4e5e7;
    --card:#f7f7f7;
    --blue-light:#2ea3dc;
    --blue:#1f7fc0;
    --blue-deep:#1a5d96;
    --charcoal:#3a3b3d;
    --text-dark:#2f3033;
    --white:#ffffff;
  }
  *{margin:0;padding:0;box-sizing:border-box}
  html,body{width:1200px;height:726px;overflow:hidden;background:var(--bg)}
  .canvas{position:relative;width:1200px;height:726px}
  .card{
    position:absolute;width:520px;height:336px;background:var(--card);
    overflow:hidden;box-shadow:0 6px 18px rgba(0,0,0,.12);
  }
  .card--front{left:50px;top:195px}
  .card--back{left:630px;top:195px}

  .wordmark{
    position:absolute;display:flex;align-items:center;gap:12px;
    font-family:"Montserrat",sans-serif;font-weight:600;color:var(--charcoal);
  }
  .wordmark__square{width:34px;height:34px;background:var(--blue)}
  .wordmark__name{font-size:30px;line-height:1;letter-spacing:2px}
  .wordmark__sub{font-size:10.5px;letter-spacing:2.6px;margin-top:6px;display:block}
  .card--front .wordmark{left:50%;top:128px;transform:translateX(-50%)}
  .card--back .wordmark{left:34px;top:160px}

  .front-stripe{position:absolute;left:0;right:0;bottom:58px;height:8px;background:var(--blue)}
  .front-stripe::after{content:"";position:absolute;left:0;right:0;top:8px;height:3px;background:var(--blue-light)}

  .wave{position:absolute;inset:0}

  .details{
    position:absolute;right:26px;top:24px;text-align:right;
    font-family:"Roboto",sans-serif;color:var(--text-dark);
  }
  .details__name{font-weight:700;font-size:20px;color:var(--blue-deep);margin-bottom:4px}
  .details__role{font-size:12px;line-height:1.35}
  .details__address{font-size:12.5px;line-height:1.4;margin-top:12px}

  .contact{
    position:absolute;right:26px;top:180px;list-style:none;
    font-family:"Roboto",sans-serif;font-size:13px;color:var(--white);text-align:right;
  }
  .contact li{display:flex;justify-content:flex-end;align-items:center;gap:8px;line-height:22px}
  .contact svg{width:12px;height:12px;fill:none;stroke:var(--white);stroke-width:1.6}
</style>
</head>
<body>
<main class="canvas">

  <section class="card card--front" aria-label="Recto de la carte">
    <div class="wordmark">
      <span class="wordmark__square"></span>
      <span><span class="wordmark__name">CLAIREVAL</span><span class="wordmark__sub">CONSEIL ET COMPTES</span></span>
    </div>
    <div class="front-stripe"></div>
  </section>

  <section class="card card--back" aria-label="Verso de la carte">
    <svg class="wave" viewBox="0 0 520 336" aria-hidden="true">
      <path d="M520,162 C425,164 340,170 302,212 C262,258 170,310 0,318 L0,336 L520,336 Z" fill="var(--blue)"/>
      <path d="M520,148 C420,150 330,155 290,200 C250,250 150,300 0,300" fill="none" stroke="var(--charcoal)" stroke-width="9"/>
      <path d="M0,326 C110,334 200,330 280,318 C220,336 100,338 0,336 Z" fill="var(--blue-light)"/>
    </svg>

    <div class="wordmark">
      <span class="wordmark__square"></span>
      <span><span class="wordmark__name">CLAIREVAL</span><span class="wordmark__sub">CONSEIL ET COMPTES</span></span>
    </div>

    <div class="details">
      <p class="details__name">Tomas Varenholt</p>
      <p class="details__role">Directeur et Fondateur</p>
      <p class="details__role">Expert-comptable diplômé</p>
      <p class="details__address">Rue des Vergières 27<br>1201 Genève</p>
    </div>

    <ul class="contact">
      <li>022 418 57 34
        <svg viewBox="0 0 12 12"><path d="M2 1.5h2.5l1 2.5-1.3 1a6 6 0 0 0 2.8 2.8l1-1.3 2.5 1V10a1 1 0 0 1-1 1A9 9 0 0 1 1 2.5a1 1 0 0 1 1-1z"/></svg></li>
      <li>tv@clairevalconseil.ch
        <svg viewBox="0 0 12 12"><rect x="1" y="2.5" width="10" height="7"/><path d="M1 2.5l5 4 5-4"/></svg></li>
      <li>www.clairevalconseil.ch
        <svg viewBox="0 0 12 12"><circle cx="6" cy="6" r="5"/><path d="M1 6h10M6 1c-2.5 3-2.5 7 0 10M6 1c2.5 3 2.5 7 0 10"/></svg></li>
    </ul>
  </section>

</main>
</body>
</html>
```